Pro work for a Landing Page for Mobile and PC in ITALIAN and ENGLISH language

We need a design for the mobile and desktop landing page you see in the enclosed text. 2 versions. We attach a copy to give an idea of style we are used to give to our landing pages, so as to understand that we are looking for quality, not only amatoriale graphic.

On Monday 1st we'll deliver design already made for the Gift Card and for TuloRix logo. We'll also provide images for the play to earn Game we talk about in second part of the Landing page

Please provide two versions: one in Italian and the other in English, Both for iOS and Android Mobile and Windows and Mac Pc.

It must be very professional work.

Precise delivery time by which design must be full ready -after usual revisions: Friday, January 5th.

Please note that no work will be accepted after this date, as it will be used on presentation the day after, Saturday January 6th

Attached at this please find Text for Landing page both in Italian and English and 3 samples from a landing page we produced and it is the way we would like present one (https://go.quillbrookwork.com/quillbrook-work-zx/).

Target Market(s)

General public, any age, income, scholarship

Industry/Entity Type

Make money Opportunity

Number of Pages Required

1 page

Font styles to use
Serif

Requirements
Must have
• Images I'll provide on Jan 1st: Zo Trevant Gift Card; TuloRix logo; KOR Play to earn Game
Nice to have
• We enclosed a landing page example. Another one is this https://events.tindrelumo.io/landing-viral/ Please note that the one we attached is the style we want for this one we are ordering.
Should not have
• Poor graphics or style. It must seem "rich"

```html
<!DOCTYPE html>
<html lang="en">
<head>
<meta charset="UTF-8">
<title>TuloRix – Zo Trevant Gift Card</title>
<link rel="stylesheet" href="https://fonts.googleapis.com/css2?family=Barlow+Condensed:wght@400;700&family=Grenze:wght@400;500&family=Michroma&display=swap">
<style>
  :root {
    --bg-deep: #0b1238;
    --bg-mid: #1a1a4a;
    --bg-violet: #3a2a5c;
    --gold: #e3bd34;
    --yellow: #fde100;
    --white: #ffffff;
    --soft-white: #d9d8e6;
    --ink: #1c1633;
    --art-cyan: #1b6d9c;
    --art-blue: #123066;
    --art-purple: #5a3e9e;
  }
  * { margin: 0; padding: 0; box-sizing: border-box; }
  html, body { width: 1200px; height: 942px; overflow: hidden; }
  body {
    background: linear-gradient(120deg, var(--bg-deep) 0%, var(--bg-mid) 55%, var(--bg-violet) 100%);
    color: var(--white);
    font-family: "Grenze", Georgia, serif;
    position: relative;
  }
  .brand {
    position: absolute;
    top: 62px; left: 0; width: 100%;
    text-align: center;
    font-family: "Barlow Condensed", "Arial Narrow", sans-serif;
    font-weight: 700;
    font-size: 62px;
    color: var(--gold);
    letter-spacing: 0.5px;
  }
  .hero-art {
    position: absolute;
    left: 60px; top: 190px;
    width: 620px; height: 690px;
    border-radius: 40px;
    background:
      radial-gradient(ellipse at 55% 45%, var(--art-cyan) 0%, var(--art-blue) 45%, transparent 75%),
      radial-gradient(ellipse at 75% 70%, var(--art-purple) 0%, transparent 55%);
  }
  .offer {
    position: absolute;
    left: 690px; top: 232px;
    width: 470px;
    text-align: center;
  }
  .offer-kicker { font-size: 30px; color: var(--soft-white); }
  .offer-title {
    font-family: "Michroma", "Arial", sans-serif;
    font-size: 46px;
    line-height: 1.1;
    margin-top: 28px;
    letter-spacing: -1px;
  }
  .offer-body { font-size: 29px; line-height: 1.25; margin-top: 36px; color: var(--soft-white); }
  .offer-title--gold { color: var(--yellow); font-size: 54px; margin-top: 40px; }
  .offer-note {
    font-family: "Barlow Condensed", "Arial Narrow", sans-serif;
    font-size: 30px;
    margin-top: 26px;
    display: inline-flex; align-items: center; gap: 10px;
  }
  .offer-note .dot { width: 22px; height: 22px; border-radius: 50%; background: var(--yellow); display: inline-block; }
  .cta {
    display: block;
    margin: 44px auto 0;
    width: 462px; height: 84px;
    background: var(--yellow);
    border-radius: 8px;
    color: var(--ink);
    font-size: 32px;
    line-height: 84px;
    text-decoration: none;
  }
  .fine-print { font-size: 23px; line-height: 1.35; margin-top: 38px; color: var(--soft-white); }
</style>
</head>
<body>
  <div class="brand">TuloRix</div>

  <div class="hero-art" role="img" aria-label="Illustration of a friendly blue robot holding a purple gift box with a yellow bow, over a glowing network backdrop"></div>

  <section class="offer">
    <p class="offer-kicker">Treat yourself to a precious gift now!</p>
    <h1 class="offer-title">ZO TREVANT</h1>
    <p class="offer-body">Yours, completely free, the Gift Card that you can use all over the world with which...</p>
    <h2 class="offer-title offer-title--gold">GIFT CARD</h2>
    <p class="offer-note">You Receive Gifts! <span class="dot"></span></p>
    <a class="cta" href="#">Request your Gift Card here for free</a>
    <p class="fine-print">From February, you will be able to download it, in a VIRTUAL version, without any costs or commitments!</p>
  </section>
</body>
</html>
```